Stationery Design Project for Marketing Consultancy

I have started a new consultancy business and require the following elements to be designed using existing logo:
• Business card
• Letterhead
• Envelope (DL, C4, C5)
• Microsoft word template for report writing
• A4 Presentation Folder
• Powerpoint template
COPY FOR FRONT AND BACK OF BUSINESS CARD
logo
'Measurable Marketing. Epic Results' slogan (but no need to use existing lockup with logo)
name, B Bus. Mktg, Grad Dip Digital Mktg, CPM (post nominal abbreviations in smaller font)
mobile: 04XX-XXX-XXX (I will give details to the winner to add)
website: www.tolvarin.com.au
email: info@tolvarin.com.au
COPY FOR LETTERHEAD
Logo
Company Name
Please, submit your designs that include business card, letterhead and envelope. Once selected the winner will be asked to complete the project by creating the rest of the artwork.
FINAL FILES
Print ready files to be supplied as well as Indesign files so that minor amends can be made if necessary in future.
• Layered vectors in EPS & PDF
• Screen quality JPEG & PNGs
ABOUT THE BUSINESS: TOLVARIN
I work with clients to understand their business challenges, developing and executing measurable marketing strategies tied to key business metrics. Services include:
Services include:
• Business planning and business development
• Marketing and brand strategy
• Insight-driven integrated campaigns
• Loyalty programs and retention marketing
• Marketing automation
• Direct marketing (traditional and digital)
• Content strategy and development
Hi everyone,
Target Market(s)
Corporate decision makers (heads of marketing, general managers etc) and small to medium sized business owners. Predominately male aged 35+
Industry/Entity Type
Marketing
Requirements
Must have
- BRAND PERSONALITY
The successful design will communicate brand personality. I am a professional, results-driven entrepreneur, but want to show off my creative flair.
MEMORABILITY
Looking for a unique and eye-catching design. Am considering special printing effects (die cuts, letterpress, interactive elements, embossing, foiling etc) or a striking minimalist approach.
Nice to have
- I have a mission that could be incorporated on reverse if room -
Turning insights into actions & passion into profit.
Should not have
- Use of pink or green.

```html
<!DOCTYPE html>
<html lang="en">
<head>
<meta charset="utf-8">
<title>Tolvarin Stationery</title>
<link rel="stylesheet" href="https://fonts.googleapis.com/css2?family=Montserrat:wght@700&family=Open+Sans:wght@400;600;700&display=swap">
<style>
  :root {
    --brand-deep: #1e5f8a;
    --brand-mid: #2479ad;
    --brand-bright: #2a93d2;
    --band-light: #3aa6cf;
    --paper: #ffffff;
    --backdrop: #e9ebec;
    --ink: #3c4650;
    --ink-soft: #7b8590;
    --on-blue: #ffffff;
    --watermark: #e3e7ea;
  }
  * { box-sizing: border-box; margin: 0; padding: 0; }
  html, body { width: 1200px; height: 859px; overflow: hidden; }
  body {
    background: var(--backdrop);
    font-family: "Open Sans", Arial, sans-serif;
    color: var(--ink);
  }
  .canvas {
    position: relative;
    width: 1200px;
    height: 859px;
    display: flex;
    gap: 30px;
    padding: 146px 30px 0;
  }
  .sheet { background: var(--paper); box-shadow: 0 2px 8px rgba(0,0,0,.12); position: relative; overflow: hidden; }

  /* wordmark lockup */
  .brand { display: flex; flex-direction: column; align-items: center; gap: 3px; }
  .brand-row { display: flex; align-items: center; gap: 6px; }
  .brand-dot { width: 12px; height: 12px; border-radius: 50%; background: var(--brand-mid); flex: none; }
  .brand-name { font-family: "Montserrat", Arial, sans-serif; font-weight: 700; color: var(--brand-mid); letter-spacing: 1px; font-size: 18px; line-height: 1.1; }
  .brand-tagline { font-size: 5.5px; font-weight: 700; letter-spacing: .6px; color: var(--brand-mid); white-space: nowrap; }
  .brand.on-blue .brand-dot { background: var(--on-blue); }
  .brand.on-blue .brand-name, .brand.on-blue .brand-tagline { color: var(--on-blue); }

  /* letterhead */
  .letterhead { width: 400px; height: 566px; padding: 44px 46px 0; }
  .letterhead .brand { margin-bottom: 26px; }
  .letter-body { font-size: 7.5px; line-height: 1.65; color: var(--ink-soft); }
  .letter-body .salutation { font-weight: 700; color: var(--ink); margin-bottom: 8px; font-size: 8px; }
  .letter-body p { margin-bottom: 9px; }
  .sign-off { margin-top: 70px; text-align: right; font-size: 7px; color: var(--ink-soft); }
  .signature { width: 90px; height: 22px; margin: 4px 0 4px auto; background: linear-gradient(90deg, transparent, #d9e2ee, transparent); }
  .sign-off .signer { font-weight: 700; color: var(--ink); font-size: 7.5px; }
  .contact-band {
    position: absolute; left: 0; right: 0; bottom: 24px; height: 16px;
    background: var(--brand-deep);
    display: flex; align-items: center; justify-content: space-around;
    padding-left: 70px;
    font-size: 5.5px; color: var(--on-blue); letter-spacing: .3px;
    white-space: nowrap;
  }
  .letterhead .band-art {
    position: absolute; left: 0; bottom: 24px; width: 64px; height: 16px; z-index: 1;
    background: linear-gradient(90deg, var(--band-light), var(--brand-bright));
  }

  /* folder */
  .folder { width: 400px; height: 566px; background: linear-gradient(160deg, var(--brand-mid), var(--brand-deep)); }
  .folder .brand { position: absolute; top: 120px; right: 40px; }
  .folder .brand-name { font-size: 24px; }
  .folder .brand-dot { width: 16px; height: 16px; }
  .folder .brand-tagline { font-size: 6.5px; }
  .folder-art {
    position: absolute; left: 0; bottom: 60px; width: 230px; height: 300px;
    background: linear-gradient(180deg, var(--brand-bright), #2f8fcc);
    border-radius: 0 140px 90px 0;
    opacity: .85;
  }

  /* right column */
  .side { width: 280px; height: 566px; display: flex; flex-direction: column; justify-content: space-between; }
  .card-pair { display: flex; gap: 10px; }
  .card { width: 135px; height: 77px; }
  .card-front { background: var(--brand-deep); color: var(--on-blue); display: flex; }
  .card-art { width: 40px; height: 100%; flex: none; background: linear-gradient(180deg, var(--brand-bright), var(--brand-mid)); border-radius: 0 28px 28px 0; }
  .card-info { padding: 7px 5px 0 7px; flex: 1; min-width: 0; }
  .card-front .brand { align-items: flex-start; gap: 2px; margin-bottom: 5px; }
  .card-front .brand-row { gap: 4px; }
  .card-front .brand-name { font-size: 10px; }
  .card-front .brand-dot { width: 7px; height: 7px; }
  .card-front .brand-tagline { font-size: 3.6px; letter-spacing: .4px; }
  .card-person { font-size: 5.5px; font-weight: 700; line-height: 1.3; }
  .card-creds { font-size: 3.4px; opacity: .85; margin-bottom: 3px; white-space: nowrap; }
  .card-contacts { font-size: 4px; line-height: 1.5; }
  .card-back { padding: 8px; }
  .card-back .holder { font-size: 5px; font-weight: 700; color: var(--brand-mid); }
  .card-back .brand { position: absolute; left: 8px; top: 26px; }
  .card-back .brand-row { gap: 4px; }
  .card-back .brand-name { font-size: 7px; }
  .card-back .brand-dot { width: 5px; height: 5px; }
  .card-watermark { position: absolute; right: -10px; bottom: -8px; width: 70px; height: 70px; border-radius: 50%; background: var(--watermark); }

  .envelope { width: 280px; height: 140px; }
  .envelope-front .brand { position: absolute; left: 40px; top: 18px; }
  .envelope-front .brand-name { font-size: 13px; }
  .envelope-front .brand-dot { width: 9px; height: 9px; }
  .envelope-front .brand-tagline { font-size: 4px; }
  .envelope-front .contact-band { bottom: 14px; height: 12px; font-size: 4.4px; padding-left: 10px; padding-right: 40px; background: linear-gradient(90deg, var(--brand-deep), var(--band-light)); }
  .envelope-front .band-art { position: absolute; right: 0; bottom: 14px; width: 34px; height: 22px; border-radius: 12px 0 0 0; background: linear-gradient(90deg, var(--band-light), var(--brand-bright)); }
  .envelope-back .flap { height: 46px; background: var(--brand-deep); }
  .envelope-back .seal { position: absolute; left: 133px; top: 54px; width: 14px; height: 14px; background: #c6d3de; }
</style>
</head>
<body>
<main class="canvas">

  <section class="sheet letterhead">
    <div class="brand">
      <div class="brand-row"><span class="brand-dot"></span><span class="brand-name">TOLVARIN</span></div>
      <span class="brand-tagline">CLEAR STRATEGY. REAL GROWTH.</span>
    </div>
    <div class="letter-body">
      <p class="salutation">Dear sir / madame,</p>
      <p>Thank you for the chance to present our proposal. We turn clear insight into measurable plans, linking every campaign to the numbers that matter most to your business and its growth.</p>
      <p>Our approach blends strategy, content and automation to reach decision makers at the right moment. Each step is tracked, reported and refined so results stay visible and easy to act on.</p>
      <p>I look forward to discussing how we can work together. Please contact me at any time to arrange a meeting.</p>
      <div class="sign-off">
        <div>Yours Sincerely,</div>
        <div class="signature" role="img" aria-label="Handwritten signature"></div>
        <div class="signer">Dana Kerrow</div>
      </div>
    </div>
    <div class="band-art" role="img" aria-label="Brand illustration accent"></div>
    <div class="contact-band">
      <span>04XX XXX XXX</span><span>info@tolvarin.com.au</span><span>www.tolvarin.com.au</span>
    </div>
  </section>

  <section class="sheet folder">
    <div class="folder-art" role="img" aria-label="Large brand illustration"></div>
    <div class="brand on-blue">
      <div class="brand-row"><span class="brand-dot"></span><span class="brand-name">TOLVARIN</span></div>
      <span class="brand-tagline">CLEAR STRATEGY. REAL GROWTH.</span>
    </div>
  </section>

  <div class="side">
    <div class="card-pair">
      <section class="sheet card card-front">
        <div class="card-art" role="img" aria-label="Brand illustration"></div>
        <div class="card-info">
          <div class="brand on-blue">
            <div class="brand-row"><span class="brand-dot"></span><span class="brand-name">TOLVARIN</span></div>
            <span class="brand-tagline">CLEAR STRATEGY. REAL GROWTH.</span>
          </div>
          <div class="card-person">Dana Kerrow</div>
          <div class="card-creds">B Bus. Mktg, Grad Dip Digital Mktg, CPM</div>
          <div class="card-contacts">04XX XXX XXX<br>info@tolvarin.com.au<br>www.tolvarin.com.au</div>
        </div>
      </section>
      <section class="sheet card card-back">
        <div class="card-watermark" role="img" aria-label="Faint brand illustration"></div>
        <div class="holder">Dana Kerrow</div>
        <div class="brand">
          <div class="brand-row"><span class="brand-dot"></span><span class="brand-name">TOLVARIN</span></div>
        </div>
      </section>
    </div>

    <section class="sheet envelope envelope-front">
      <div class="brand">
        <div class="brand-row"><span class="brand-dot"></span><span class="brand-name">TOLVARIN</span></div>
        <span class="brand-tagline">CLEAR STRATEGY. REAL GROWTH.</span>
      </div>
      <div class="contact-band">
        <span>04XX XXX XXX</span><span>info@tolvarin.com.au</span><span>www.tolvarin.com.au</span>
      </div>
      <div class="band-art" role="img" aria-label="Brand illustration accent"></div>
    </section>

    <section class="sheet envelope envelope-back">
      <div class="flap"></div>
      <div class="seal"></div>
    </section>
  </div>

</main>
</body>
</html>
```